Exec Conference Design Concept

We need to refresh & update nonprofit association graphic design for annual meeting. The graphics will be used to promote the event primarily through digital communications & social media. Other materials we generate for this event are the agenda & billboard content. You can view the existing design at www.lutavorin.org under Events.

The target audience is primarily male, ages 35-60 in executive positions in C-Corps. The conference topics center on manufacturing regulations, marketing trends, and the economy. This conference has been around almost 30 years so we need something to invigorate potential registrants that will get their attention. It still needs to be professional and business-like.

In addition to a new design concept we would like to update the color palette. We’ve attached some mood boards with potential color & font suggestions. Our company logo is also attached and is the only design element tied to our branding that cannot be changed.

Designs should be energetic and sophisticated. Ideally, we would like the designs in Adobe Indesign or Photoshop. However, we can work with Illustrator.

Target Market(s)

Male business executives age 35-60.

Industry/Entity Type

Polystyrene manufacturing industry supply chain.

Other font styles liked:
• I usually prefer sans serif

Requirements
Must have
• Focus points to draw attention to higher level informational units. For example, some people will only read the headers and not detailed copy.
Nice to have
• Ways to insert bonus content that don’t over power other content. I like to see a good use of white space to enhance readability.

```html
<!DOCTYPE html>
<html lang="en">
<head>
<meta charset="utf-8">
<title>Luta Expo 2026 – Navigating the Business of Tomorrow</title>
<link rel="stylesheet" href="https://fonts.googleapis.com/css2?family=Barlow+Condensed:wght@300;400;500;600;700&family=Montserrat:wght@400;500&display=swap">
<style>
  :root{
    --brown:#463c2b;
    --ink:#1f1a14;
    --lime:#93bd0f;
    --olive:#6b8c4c;
    --stone:#ebe9e6;
    --page:#f1f1f1;
    --white:#ffffff;
    --body-text:#2a2520;
    --rule:#9bb08a;
  }
  *{margin:0;padding:0;box-sizing:border-box}
  html,body{width:766px;height:1200px;overflow:hidden;background:var(--page)}
  .flyer{position:absolute;left:62px;top:18px;width:641px;height:1164px;background:var(--white);overflow:hidden;font-family:"Barlow Condensed",sans-serif;color:var(--brown)}
  .abs{position:absolute}

  .brand{left:0;width:641px;top:84px;display:flex;justify-content:center;align-items:center;gap:10px}
  .brand-square{width:34px;height:34px;background:var(--lime);border-radius:6px}
  .brand-name{font-weight:700;font-size:40px;line-height:1;color:var(--brown);letter-spacing:.5px}

  .headline{left:85px;top:181px;width:480px;font-weight:700;font-size:50px;line-height:46px;letter-spacing:.2px;color:var(--brown)}
  .event-tag{left:358px;top:236px;width:196px;height:36px;border:1.5px solid var(--lime);color:var(--lime);font-size:28px;font-weight:300;display:flex;align-items:center;justify-content:center;gap:6px;line-height:1}
  .event-tag b{font-weight:700}
  .tagline{left:0;top:290px;width:641px;text-align:center;white-space:nowrap;font-weight:600;font-size:19px;letter-spacing:0;color:var(--ink)}

  .band{left:0;width:641px;height:9px;background:var(--olive)}
  .hero{left:0;top:354px;width:641px;height:296px;background:linear-gradient(100deg,#8c9aa8 0%,#c9ccc9 30%,#f1f1ef 45%,#b9a65a 58%,#d8d6cf 72%,#3f74c2 100%)}

  .topics{left:0;top:650px;width:641px;height:252px;background:var(--stone)}
  .topic-head{top:14px;width:200px}
  .topic-head svg{display:block;margin:0 auto;width:46px;height:44px}
  .topic-head h2{margin-top:14px;text-align:center;font-weight:600;font-size:26px;line-height:22px;letter-spacing:.2px;color:var(--brown)}
  .topic-list{top:131px;width:150px;list-style:none;padding-left:9px}
  .topic-list::before{content:"";position:absolute;left:0;top:6px;height:33px;border-left:1px solid var(--rule)}
  .topic-list li{position:relative;font-family:"Montserrat",sans-serif;font-size:10.4px;line-height:12.6px;color:var(--body-text);margin-bottom:7.5px}
  .topic-list li::before{content:"";position:absolute;left:-11.5px;top:3.5px;width:5px;height:5px;border-radius:50%;background:var(--stone);border:1px solid var(--olive)}

  .register{left:181px;top:874px;width:280px;height:53px;border-radius:22px;background:var(--lime);color:var(--white);font-weight:600;font-size:31px;display:flex;align-items:center;justify-content:center;letter-spacing:.4px}

  .bonus{left:46px;top:953px;width:549px;height:127px;border:1.6px solid var(--olive)}
  .bonus-corner{right:-1px;top:-1px;width:34px;height:34px}
  .newsletter-cover{left:28px;top:25px;width:108px;height:79px;background:linear-gradient(90deg,var(--olive) 0%,var(--olive) 78%,#8fbf3a 80%,#6f8fa8 84%,#c9cbc8 100%)}
  .cover-brand{left:10px;top:14px;font-weight:700;font-size:6px;color:var(--white);display:flex;gap:3px;align-items:center}
  .cover-brand i{display:block;width:7px;height:7px;background:var(--lime)}
  .cover-title{left:10px;top:32px;font-weight:600;font-size:7.2px;line-height:8.2px;color:var(--white)}
  .cover-url{left:10px;top:67px;font-size:3.5px;color:#e3ead8}
  .bonus-title{left:168px;top:20px;font-weight:600;font-size:24.5px;line-height:1;color:var(--brown);white-space:nowrap}
  .bonus-copy{left:168px;top:46px;width:360px;font-family:"Montserrat",sans-serif;font-size:10.6px;line-height:13px;color:var(--body-text)}
  .bonus-link{left:168px;top:84px;font-family:"Montserrat",sans-serif;font-weight:500;font-size:13.6px;color:var(--olive);text-decoration:underline;text-underline-offset:2px;white-space:nowrap}

  .footer{left:0;top:1098px;width:641px;height:57px;background:var(--stone)}
  .social{left:46px;top:18px;display:flex;gap:6px}
  .social span{display:block;width:21px;height:21px;border-radius:50%;background:var(--brown)}
  .contact{right:46px;top:19px;font-size:14px;letter-spacing:.5px;color:var(--brown);white-space:nowrap}
</style>
</head>
<body>
<main class="flyer">
  <div class="abs brand"><span class="brand-square"></span><span class="brand-name">LUTA EXPO 2026</span></div>

  <h1 class="abs headline">NAVIGATING THE BUSINESS<br>OF TOMORROW</h1>
  <div class="abs event-tag">LUTA EXPO <b>2026</b></div>
  <p class="abs tagline">DECADES OF LEADERSHIP, REIMAGINED FOR THE MODERN EXECUTIVE</p>

  <div class="abs band" style="top:345px"></div>
  <div class="abs hero" role="img" aria-label="Photo of a worker stacking white foam boxes on a pallet in a factory with a forklift and blue machinery"></div>

  <section class="abs topics">
    <div class="abs topic-head" style="left:31px">
      <svg viewBox="0 0 46 44" fill="none" stroke="#6b8c4c" stroke-width="1.4">
        <path d="M23 3l3 4 5-1 1 5 5 2-2 5 3 4-4 3 1 5-5 1-1 5-5-1-3 4-3-4-5 1-1-5-5-1 1-5-4-3 3-4-2-5 5-2 1-5 5 1z"/>
        <circle cx="23" cy="22" r="11"/>
        <circle cx="19" cy="18" r="2.5"/><circle cx="27" cy="26" r="2.5"/><circle cx="19" cy="26" r="2"/><circle cx="27" cy="18" r="2"/>
        <path d="M17 28l12-12"/>
      </svg>
      <h2>MANUFACTURING<br>REGULATIONS</h2>
    </div>
    <ul class="abs topic-list" style="left:57px"><li>Compliance in a changing world</li><li>Policy impact on production</li></ul>

    <div class="abs topic-head" style="left:235px">
      <svg viewBox="0 0 46 44" fill="none" stroke="#6b8c4c" stroke-width="1.4">
        <path d="M5 17h8l14-10v26L13 25H5z"/>
        <path d="M9 25l3 11h4l-2-11"/>
        <path d="M27 13a5 5 0 010 10"/>
        <path d="M33 9l4-3M34 18h6M33 27l4 3"/>
      </svg>
      <h2>MARKETING<br>TRENDS</h2>
    </div>
    <ul class="abs topic-list" style="left:269px"><li>Data-driven customer growth</li><li>Digital transformation strategies</li></ul>

    <div class="abs topic-head" style="left:426px">
      <svg viewBox="0 0 46 44" fill="none" stroke="#6b8c4c" stroke-width="1.4">
        <path d="M4 40h40"/>
        <rect x="7" y="28" width="5" height="12"/><rect x="16" y="24" width="5" height="16"/><rect x="25" y="26" width="5" height="14"/><rect x="34" y="16" width="5" height="24"/>
        <path d="M5 22l10-8 9 4 14-12"/><path d="M33 5h6v6"/>
      </svg>
      <h2>ECONOMIC<br>OUTLOOK</h2>
    </div>
    <ul class="abs topic-list" style="left:468px;width:130px"><li>Market risks and opportunities</li><li>Forecasting industry growth</li></ul>
  </section>

  <a class="abs register">REGISTER TODAY</a>

  <section class="abs bonus">
    <svg class="abs bonus-corner" viewBox="0 0 34 34"><path d="M0 0h34v34z" fill="#6b8c4c"/></svg>
    <div class="abs newsletter-cover" role="img" aria-label="Newsletter cover with a factory photo">
      <div class="abs cover-brand"><i></i>LUTA EXPO</div>
      <div class="abs cover-title">DOWNLOAD OUR<br>EXCLUSIVE MONTHLY<br>NEWSLETTER</div>
      <div class="abs cover-url">www.lutavorin.org</div>
    </div>
    <h3 class="abs bonus-title">BONUS CONTENT: EXECUTIVE INSIGHTS</h3>
    <p class="abs bonus-copy">Exclusive insights from industry leaders to help you navigate change, adapt faster, and stay ahead.</p>
    <a class="abs bonus-link">Download Our Exclusive Monthly Newsletter</a>
  </section>

  <footer class="abs footer">
    <div class="abs social" aria-label="Social media"><span></span><span></span><span></span></div>
    <div class="abs contact">(555) 014-2290 &nbsp;|&nbsp; www.lutavorin.org</div>
  </footer>
  <div class="abs band" style="top:1155px"></div>
</main>
</body>
</html>
```